Redesign of business card for Cedar Ridge Mechanical

We are looking for a new design for our business cards for Cedar Ridge Mechanical. We are a plumbing & HVAC construction company, operating on the West Coast of Canada and USA. Logo attached.
Industry/Entity Type
Construction - Plumbing & HVAC
Contact Information for Business Card
Name, address, phone numbers, email, website address
Look and feel
Each slider illustrates characteristics of the customer's brand and the style your logo design should communicate.

```html
<!DOCTYPE html>
<html lang="en">
<head>
<meta charset="UTF-8">
<title>Cedar Ridge Mechanical – Business Card</title>
<link rel="stylesheet" href="https://fonts.googleapis.com/css2?family=Montserrat:wght@400;700&display=swap">
<style>
  :root {
    --page-bg: #3a3330;
    --card-bg: #1f1f1f;
    --card-back-bg: #1b1b1b;
    --ink-light: #ffffff;
    --ink-muted: #cfcfcf;
    --ink-gloss: #0b0b0b;
    --rule: #e6e6e6;
  }
  * { box-sizing: border-box; margin: 0; padding: 0; }
  html, body {
    width: 1200px;
    height: 786px;
    overflow: hidden;
  }
  body {
    background: var(--page-bg);
    font-family: "Montserrat", sans-serif;
    display: flex;
    align-items: center;
    justify-content: center;
    gap: 40px;
  }
  .card {
    width: 540px;
    height: 309px;
    border-radius: 4px;
    box-shadow: 0 10px 30px rgba(0,0,0,0.45);
    position: relative;
  }
  /* Front: brand + contact */
  .card-front {
    background: var(--card-bg);
    display: flex;
    align-items: center;
    padding: 0 34px;
  }
  .brand {
    width: 200px;
    display: flex;
    align-items: center;
    gap: 10px;
    color: var(--ink-light);
    font-weight: 700;
    font-size: 17px;
    line-height: 1.2;
  }
  .brand-square {
    flex: none;
    width: 14px;
    height: 14px;
    background: var(--ink-light);
  }
  .divider {
    width: 2px;
    height: 150px;
    background: var(--rule);
    margin: 0 20px 0 12px;
  }
  .contact { color: var(--ink-light); }
  .contact-name {
    font-weight: 700;
    font-size: 17px;
    letter-spacing: 0.2px;
  }
  .contact-role {
    font-size: 11px;
    color: var(--ink-muted);
    margin-bottom: 12px;
  }
  .contact-address {
    font-size: 11px;
    color: var(--ink-muted);
    line-height: 1.35;
    margin-bottom: 10px;
  }
  .contact-list { list-style: none; }
  .contact-list li {
    display: flex;
    align-items: center;
    gap: 10px;
    font-size: 11.5px;
    color: var(--ink-light);
    margin-bottom: 7px;
  }
  .contact-list svg {
    width: 11px;
    height: 11px;
    flex: none;
    fill: var(--ink-light);
  }
  /* Back: brand only */
  .card-back {
    background: var(--card-back-bg);
    display: flex;
    align-items: center;
    justify-content: center;
  }
  .brand-back {
    display: flex;
    align-items: center;
    gap: 14px;
    color: var(--ink-gloss);
    font-weight: 700;
    font-size: 28px;
    letter-spacing: 0.5px;
    text-transform: uppercase;
    text-align: left;
    line-height: 1.15;
  }
  .brand-back .brand-square {
    width: 22px;
    height: 22px;
    background: var(--ink-gloss);
  }
</style>
</head>
<body>
  <article class="card card-front">
    <div class="brand">
      <span class="brand-square"></span>
      <span class="brand-name">Cedar Ridge Mechanical</span>
    </div>
    <div class="divider"></div>
    <div class="contact">
      <p class="contact-name">Daniel Reyes</p>
      <p class="contact-role">Managing Director</p>
      <p class="contact-address">245 Harbor View Road<br>Salem, OR 97301</p>
      <ul class="contact-list">
        <li>
          <svg viewBox="0 0 24 24" aria-hidden="true"><path d="M6.6 10.8a15 15 0 0 0 6.6 6.6l2.2-2.2a1 1 0 0 1 1-.25 11.4 11.4 0 0 0 3.6.57 1 1 0 0 1 1 1V20a1 1 0 0 1-1 1A17 17 0 0 1 3 4a1 1 0 0 1 1-1h3.5a1 1 0 0 1 1 1c0 1.25.2 2.45.57 3.57a1 1 0 0 1-.25 1z"/></svg>
          555.014.2290
        </li>
        <li>
          <svg viewBox="0 0 24 24" aria-hidden="true"><path d="M2 5h20v14H2z M3 6l9 7 9-7" fill="none" stroke="#fff" stroke-width="2.2"/></svg>
          info@cedarridgemechanical.com
        </li>
        <li>
          <svg viewBox="0 0 24 24" aria-hidden="true"><circle cx="12" cy="12" r="9" fill="none" stroke="#fff" stroke-width="2.2"/><path d="M3 12h18M12 3c3 3 3 15 0 18M12 3c-3 3-3 15 0 18" fill="none" stroke="#fff" stroke-width="1.6"/></svg>
          www.cedarridgemechanical.com
        </li>
      </ul>
    </div>
  </article>

  <article class="card card-back">
    <div class="brand-back">
      <span class="brand-square"></span>
      <span class="brand-name">Cedar Ridge<br>Mechanical</span>
    </div>
  </article>
</body>
</html>
```